Indy Film Production Company/Studio

We need a business card designed from an existing logo. We are a digital studio/production company that caters to creating genre entertainment, like Action, Horror, and martial arts. The card along with the logo will be used to Brand the company from letter heads to banners. The design will also be used for postcards and Brochures. It should be professional and masculine.
Updates

Thank you to all the designers who have participated. I'm narrowing down who it will be. Thank you again.

Target Market(s)

Investors, Networks, Producers, and actors

Industry/Entity Type

Film Production

Contact Information for Business Card

Teodoro Valbuena
Producer/Writer/Director
www.kestrelpicturehouse.example

Requirements
Must have
• Website address, Facebook icon and Twitter icon possibly in the back of the card.
Nice to have
• Logline of Company: Follow The Action.

```html
<!DOCTYPE html>
<html lang="en">
<head>
<meta charset="utf-8">
<title>Kestrel Picture House – Business Card</title>
<link href="https://fonts.googleapis.com/css2?family=Lato:wght@400;700;900&display=swap" rel="stylesheet">
<style>
  :root {
    --brand-red: #ee1c25;
    --paper-white: #ffffff;
    --page-bg: #e9e6e2;
    --card-shadow: rgba(0, 0, 0, 0.18);
  }
  * { box-sizing: border-box; margin: 0; padding: 0; }
  html, body {
    width: 1200px;
    height: 900px;
    overflow: hidden;
    background: var(--page-bg);
    font-family: "Lato", sans-serif;
  }
  .stage {
    width: 1200px;
    height: 900px;
    display: flex;
    align-items: center;
    justify-content: center;
    gap: 40px;
  }
  .card {
    position: relative;
    width: 540px;
    height: 309px;
    overflow: hidden;
    box-shadow: 0 6px 18px var(--card-shadow);
  }
  /* Front side */
  .card--front {
    background: var(--brand-red);
    display: flex;
    align-items: center;
    justify-content: center;
  }
  .wordmark {
    font-family: "Lato", sans-serif;
    font-weight: 900;
    text-transform: uppercase;
    text-align: center;
    line-height: 0.95;
    letter-spacing: 1px;
  }
  .wordmark__line { display: block; }
  .card--front .wordmark { color: var(--paper-white); font-size: 40px; }
  /* Back side */
  .card--back { background: var(--paper-white); }
  .back__logo-area {
    position: absolute;
    left: 0; top: 0;
    width: 540px; height: 170px;
    display: flex;
    align-items: center;
    justify-content: center;
    padding-left: 90px;
  }
  .card--back .wordmark { color: var(--brand-red); font-size: 34px; }
  .back__info-band {
    position: absolute;
    left: 0; top: 170px;
    width: 540px; height: 139px;
    background: var(--brand-red);
    color: var(--paper-white);
  }
  .person {
    position: absolute;
    right: 280px;
    top: 18px;
    text-align: right;
  }
  .person__name { font-size: 20px; font-weight: 400; line-height: 1.1; }
  .person__title { font-size: 13px; margin-top: 3px; }
  .person__address { font-size: 13px; line-height: 1.35; margin-top: 10px; }
  .contact-list {
    position: absolute;
    left: 280px;
    top: 8px;
    list-style: none;
    font-size: 12px;
  }
  .contact-list__item {
    display: flex;
    align-items: center;
    gap: 7px;
    height: 20px;
  }
  .contact-icon { width: 13px; height: 13px; flex: none; }
</style>
</head>
<body>
<main class="stage">
  <section class="card card--front" aria-label="Business card front">
    <div class="wordmark">
      <span class="wordmark__line">Kestrel</span>
      <span class="wordmark__line">Picture House</span>
    </div>
  </section>

  <section class="card card--back" aria-label="Business card back">
    <div class="back__logo-area">
      <div class="wordmark">
        <span class="wordmark__line">Kestrel</span>
        <span class="wordmark__line">Picture House</span>
      </div>
    </div>
    <div class="back__info-band">
      <div class="person">
        <p class="person__name">Teodoro Valbuena</p>
        <p class="person__title">Managing Director</p>
        <p class="person__address">1234, Address GoesHere<br>Country, 12345</p>
      </div>
      <ul class="contact-list">
        <li class="contact-list__item">
          <svg class="contact-icon" viewBox="0 0 13 13" aria-hidden="true">
            <rect width="13" height="13" rx="2" fill="#fff"/>
            <path d="M3 4.5c1.5-2 5.5-2 7 0l-1 1.2-1.3-.6v-.8h-2.4v.8l-1.3.6z M4 7h5v3H4z" fill="#ee1c25"/>
          </svg>
          <span>123-456-7890</span>
        </li>
        <li class="contact-list__item">
          <svg class="contact-icon" viewBox="0 0 13 13" aria-hidden="true">
            <rect width="13" height="13" rx="2" fill="#fff"/>
            <rect x="4" y="2.5" width="5" height="3" fill="#ee1c25"/>
            <rect x="2.5" y="5.5" width="8" height="3.5" fill="#ee1c25"/>
            <rect x="4" y="8" width="5" height="2.5" fill="#ee1c25"/>
          </svg>
          <span>123-456-7890</span>
        </li>
        <li class="contact-list__item">
          <svg class="contact-icon" viewBox="0 0 13 13" aria-hidden="true">
            <rect width="13" height="13" rx="2" fill="#fff"/>
            <rect x="2.5" y="3.5" width="8" height="6" fill="#ee1c25"/>
            <path d="M2.8 3.8l3.7 3 3.7-3" fill="none" stroke="#fff" stroke-width="0.9"/>
          </svg>
          <span>info@kestrelpicture.example</span>
        </li>
        <li class="contact-list__item">
          <svg class="contact-icon" viewBox="0 0 13 13" aria-hidden="true">
            <rect width="13" height="13" rx="2" fill="#fff"/>
            <path d="M5.2 7.8l2.6-2.6" stroke="#ee1c25" stroke-width="1.2"/>
            <rect x="2.2" y="6.4" width="4" height="2.6" rx="1.3" transform="rotate(-45 4.2 7.7)" fill="none" stroke="#ee1c25" stroke-width="1.1"/>
            <rect x="6.8" y="4" width="4" height="2.6" rx="1.3" transform="rotate(-45 8.8 5.3)" fill="none" stroke="#ee1c25" stroke-width="1.1"/>
          </svg>
          <span>www.kestrelpicturehouse.example</span>
        </li>
      </ul>
    </div>
  </section>
</main>
</body>
</html>
```